Road Construction Company needs business cards

We would like a new business card designed for our business.

We're a road construction company based in Qld, Australia.

Can the business card please have the following information on it.

Name: Warren Halbeck
Position: General Manager
Phone: 0472 915 348
Email: Warren.halbeck@tovrin.com.au
Address: 87 Marrow Ave, Pendlebay, QLD, 4023
Website: www.tovrin.com.au

Visually we'd like the card to be professional and simple.

Attached is our logo.

Our website is www.tovrin.com.au

Target Market(s)

Men aged 25-60

Contact Information for Business Card

As listed in project description

Font styles to use
Serif

Requirements
Must have
• Large logo on back of card

```html
<!DOCTYPE html>
<html lang="en">
<head>
<meta charset="utf-8">
<title>Tovrin Business Card</title>
<link rel="stylesheet" href="https://fonts.googleapis.com/css2?family=Figtree:wght@400;700;800&display=swap">
<style>
  :root {
    --page-bg: #e4e4e4;
    --brand-blue: #0d55a3;
    --brand-blue-dark: #08479a;
    --brand-navy: #0b3f8f;
    --curve-indigo: #3551a2;
    --curve-sky: #2fb8e4;
    --card-white: #f1f1f1;
    --text-grey: #55595e;
  }
  * { box-sizing: border-box; margin: 0; padding: 0; }
  html, body { width: 1200px; height: 1200px; overflow: hidden; }
  body {
    background: var(--page-bg);
    font-family: "Figtree", Arial, sans-serif;
    position: relative;
  }
  .card {
    position: absolute;
    left: 234px;
    width: 731px;
    height: 418px;
    overflow: hidden;
  }
  .card-front {
    top: 160px;
    background: linear-gradient(100deg, var(--brand-blue-dark) 0%, var(--brand-blue) 50%, #1565a8 100%);
    display: flex;
    align-items: center;
    justify-content: center;
  }
  .front-wordmark {
    color: #f3f1ee;
    font-weight: 800;
    font-size: 96px;
    letter-spacing: 4px;
    line-height: 1;
    margin-top: -70px;
  }
  .card-back {
    top: 632px;
    background: linear-gradient(110deg, #ececec 0%, var(--card-white) 60%, #f4f4f4 100%);
  }
  .back-curves { position: absolute; inset: 0; width: 100%; height: 100%; }
  .person-name {
    position: absolute; left: 55px; top: 52px;
    color: var(--brand-navy);
    font-weight: 700; font-size: 31px; line-height: 1;
  }
  .person-role {
    position: absolute; left: 56px; top: 89px;
    color: var(--text-grey);
    font-size: 19px; line-height: 1;
  }
  .back-wordmark {
    position: absolute; right: 53px; top: 50px;
    color: var(--brand-navy);
    font-weight: 800; font-size: 38px; letter-spacing: 2px; line-height: 1;
  }
  .address {
    position: absolute; left: 55px; top: 210px;
    color: var(--text-grey);
    font-size: 19px; line-height: 27px;
  }
  .contact-list {
    position: absolute; left: 54px; top: 283px;
    list-style: none;
    color: var(--text-grey);
    font-size: 19px;
  }
  .contact-list li {
    display: flex; align-items: center; gap: 9px;
    height: 28px;
  }
  .contact-list svg { width: 16px; height: 16px; fill: var(--brand-navy); flex: none; }
</style>
</head>
<body>
  <section class="card card-front">
    <div class="front-wordmark">TOVRIN</div>
  </section>

  <section class="card card-back">
    <svg class="back-curves" viewBox="0 0 731 418" preserveAspectRatio="none" aria-hidden="true">
      <path d="M412 418 C560 410 690 320 731 180 L731 418 Z" fill="var(--curve-indigo)"/>
      <path d="M468 418 C600 405 700 340 731 268 L731 418 Z" fill="var(--curve-sky)"/>
    </svg>

    <h1 class="person-name">Warren Halbeck</h1>
    <p class="person-role">General Manager</p>
    <div class="back-wordmark">TOVRIN</div>

    <p class="address">87 Marrow Ave, Pendlebay,<br>QLD, 4023</p>

    <ul class="contact-list">
      <li>
        <svg viewBox="0 0 24 24"><path d="M6.6 10.8a15.1 15.1 0 0 0 6.6 6.6l2.2-2.2c.3-.3.7-.4 1-.2 1.1.4 2.3.6 3.6.6.6 0 1 .4 1 1V20c0 .6-.4 1-1 1C10.6 21 3 13.4 3 4c0-.6.4-1 1-1h3.5c.6 0 1 .4 1 1 0 1.3.2 2.5.6 3.6.1.3 0 .7-.2 1z"/></svg>
        0472 915 348
      </li>
      <li>
        <svg viewBox="0 0 24 24"><path d="M2 5h20v14H2z M3.5 6.5 12 12.5l8.5-6z" fill-rule="evenodd"/></svg>
        Warren.halbeck@tovrin.com.au
      </li>
      <li>
        <svg viewBox="0 0 24 24"><path d="M12 2a10 10 0 1 0 0 20 10 10 0 0 0 0-20zm6.9 9h-3a15 15 0 0 0-1.3-5.6A8 8 0 0 1 18.9 11zM12 4.1c.9 1.2 1.8 3.5 1.9 6.9h-3.8c.1-3.4 1-5.7 1.9-6.9zM9.4 5.4A15 15 0 0 0 8.1 11h-3a8 8 0 0 1 4.3-5.6zM5.1 13h3a15 15 0 0 0 1.3 5.6A8 8 0 0 1 5.1 13zm6.9 6.9c-.9-1.2-1.8-3.5-1.9-6.9h3.8c-.1 3.4-1 5.7-1.9 6.9zm2.6-1.3a15 15 0 0 0 1.3-5.6h3a8 8 0 0 1-4.3 5.6z"/></svg>
        www.tovrin.com.au
      </li>
    </ul>
  </section>
</body>
</html>
```